Korval Advise Business Cards

We need a business card design for Korval Advise (Logo Attached), a management consultancy specialized in brand & business building.

Design should be clean, smart and a touch of innnovation without being gimmicky.

The details on the card should be:
Name: Tomas Velduren
Title: Managing Director
Address: 42 Marlowe Pier, Tarn Vessel Tower, Singapore 073926
Tel: +6285927461082
email: tv@korvaladvise.example
website: korvaladvise.example

For further background on corporate identity, please check www.korvaladvise.example
Updates

Dear all,

Many thanks for the submissions so far! I gave feedback to those designs that I prefer at this stage.

Overall I see that my preference goes into the direction that 'less is more' and 'simple is beautiful'

Please create uniqueness and standout by the simplicity and attraction of the overall concept and design.

Many thanks and please shout incase of questions!

Tomas

Industry/Entity Type

Business

```html
<!DOCTYPE html>
<html lang="en">
<head>
<meta charset="utf-8">
<title>Korval Advise Business Cards</title>
<link href="https://fonts.googleapis.com/css2?family=Open+Sans:wght@400;600;700&display=swap" rel="stylesheet">
<style>
  :root {
    --charcoal: #4b4b4b;
    --orange: #ff6a00;
    --paper: #ffffff;
    --backdrop: #ececec;
    --text-grey: #555555;
  }
  * { box-sizing: border-box; margin: 0; padding: 0; }
  html, body {
    width: 1173px; height: 1200px; overflow: hidden;
    background: var(--backdrop);
    font-family: "Open Sans", Arial, sans-serif;
  }
  .canvas { position: relative; width: 1173px; height: 1200px; }

  .card { position: absolute; overflow: hidden; box-shadow: 0 3px 10px rgba(0,0,0,.18); }

  .card-front {
    left: 184px; top: 56px; width: 944px; height: 538px;
    background: var(--paper);
  }
  .card-front .swoosh { position: absolute; inset: 0; }
  .swoosh .band-grey { fill: var(--charcoal); }
  .swoosh .band-orange { fill: var(--orange); }

  .wordmark {
    position: absolute; font-weight: 600; white-space: nowrap; line-height: 1;
  }
  .card-front .wordmark {
    left: 44px; top: 62px; font-size: 80px; color: var(--charcoal);
  }

  .holder { position: absolute; left: 44px; top: 306px; color: var(--text-grey); }
  .holder-name { font-size: 30px; font-weight: 700; line-height: 1.2; }
  .holder-title { font-size: 23px; color: var(--orange); line-height: 1.4; }
  .holder-address { margin-top: 34px; font-size: 23px; line-height: 34px; }

  .contacts {
    position: absolute; right: 37px; top: 384px;
    list-style: none; color: var(--paper); font-size: 23px; text-align: right;
  }
  .contacts li { display: flex; align-items: center; justify-content: flex-end; gap: 8px; height: 41px; }
  .contacts svg { width: 20px; height: 20px; flex: none; }
  .contacts svg * { fill: none; stroke: var(--paper); stroke-width: 1.8; stroke-linecap: round; stroke-linejoin: round; }

  .card-back {
    left: 38px; top: 627px; width: 941px; height: 538px;
    background: var(--charcoal); color: var(--paper);
  }
  .card-back .wordmark {
    left: 0; right: 0; top: 212px; text-align: center; font-size: 104px;
  }
  .card-back .site {
    position: absolute; left: 0; right: 0; top: 408px; text-align: center;
    font-size: 26px; letter-spacing: 0.22em;
  }
</style>
</head>
<body>
<main class="canvas">

  <section class="card card-front" aria-label="Business card front">
    <svg class="swoosh" viewBox="0 0 944 538" preserveAspectRatio="none" aria-hidden="true">
      <path class="band-grey" d="M819 0 L944 0 L944 538 L276 538 Q790 390 819 0 Z"/>
      <path class="band-orange" d="M944 52 L944 538 L292 538 Q830 420 944 52 Z"/>
    </svg>

    <div class="wordmark">Korval Advise</div>

    <div class="holder">
      <p class="holder-name">Tomas Velduren</p>
      <p class="holder-title">Managing Director</p>
      <p class="holder-address">42 Marlowe Pier, Tarn<br>Vessel Tower<br>Singapore 073926</p>
    </div>

    <ul class="contacts">
      <li>
        <svg viewBox="0 0 20 20" aria-hidden="true"><circle cx="10" cy="10" r="8"/><path d="M7 6 Q6 11 11 14 L13 12"/></svg>
        +6285927461082
      </li>
      <li>
        <svg viewBox="0 0 20 20" aria-hidden="true"><rect x="2" y="5" width="16" height="11" rx="1"/><path d="M2 6 L10 12 L18 6"/></svg>
        tv@korvaladvise.example
      </li>
      <li>
        <svg viewBox="0 0 20 20" aria-hidden="true"><circle cx="10" cy="10" r="8"/><ellipse cx="10" cy="10" rx="3.5" ry="8"/><path d="M2 10 H18"/></svg>
        www.korvaladvise.example
      </li>
    </ul>
  </section>

  <section class="card card-back" aria-label="Business card back">
    <div class="wordmark">Korval Advise</div>
    <p class="site">www.korvaladvise.example</p>
  </section>

</main>
</body>
</html>
```